Corvane Capital Business Cards

These are professional business cards that are for my family office.
Put fake emails and phone numbers as of now until I finalize those components. This family office controls my families investments, assets, and future. The cards should be professional.
..
.
.
.
I just uploaded another variation of a logo I would like to see as a business card to I am inbeteen which logo to use

Target Market(s)

business

Industry/Entity Type

business

Contact Information for Business Card

Professional, wealth related, finance related.

Requirements
Must have
• Logo

```html
<!DOCTYPE html>
<html lang="en">
<head>
<meta charset="UTF-8">
<title>Corvane Capital Business Card</title>
<link rel="stylesheet" href="https://fonts.googleapis.com/css2?family=Lato:wght@400;700;900&display=swap">
<style>
  :root {
    --page-bg: #e8e5e1;
    --frost-light: #f4f3f1;
    --frost-mid: #d9d6d2;
    --panel-dark: #0d0f14;
    --panel-edge: #2a2d34;
    --ring-grey: #b7b8bb;
    --name-grey: #8b8e94;
    --text-light: #d6d8dc;
    --icon-grey: #9a9ca1;
    --logo-ink: #2b2e35;
  }
  * { margin: 0; padding: 0; box-sizing: border-box; }
  html, body {
    width: 1200px; height: 900px; overflow: hidden;
    background: var(--page-bg);
    font-family: "Lato", Arial, sans-serif;
  }
  .business-card {
    position: absolute; left: 100px; top: 162px;
    width: 1000px; height: 575px;
    border-radius: 18px; overflow: hidden;
    background: linear-gradient(135deg, var(--frost-light), var(--frost-mid));
    box-shadow: 0 10px 30px rgba(0,0,0,0.15);
  }
  .card-shapes { position: absolute; inset: 0; }
  .brand-mark {
    position: absolute; left: 281px; top: 281px;
    transform: translate(-50%, -50%);
    display: flex; flex-direction: column; align-items: center; gap: 26px;
  }
  .brand-circle {
    width: 150px; height: 150px; border-radius: 50%;
    border: 5px solid var(--logo-ink);
  }
  .brand-name {
    font-weight: 700; font-size: 44px; color: var(--logo-ink);
    letter-spacing: 1px; white-space: nowrap;
  }
  .contact-block { position: absolute; left: 617px; top: 100px; }
  .person-name {
    font-weight: 900; font-size: 38px; color: var(--name-grey);
    letter-spacing: 1px; line-height: 1;
  }
  .person-title {
    margin-top: 10px; font-size: 22px; color: var(--text-light);
  }
  .divider-dots { display: flex; gap: 6px; margin: 24px 0 22px; }
  .divider-dots span {
    width: 10px; height: 10px; border-radius: 50%; background: var(--icon-grey);
  }
  .contact-list { list-style: none; }
  .contact-list li {
    display: flex; align-items: flex-start; gap: 12px;
    font-size: 20.5px; color: var(--text-light); line-height: 33px;
  }
  .contact-list li.address { margin-bottom: 8px; }
  .contact-list svg { width: 18px; height: 18px; margin-top: 8px; flex: none; fill: var(--icon-grey); }
</style>
</head>
<body>
  <div class="business-card">
    <svg class="card-shapes" viewBox="0 0 1000 575" aria-hidden="true">
      <defs>
        <linearGradient id="panelGradient" x1="0" y1="0" x2="1" y2="1">
          <stop offset="0" stop-color="#05070b"/>
          <stop offset="0.6" stop-color="#10131a"/>
          <stop offset="1" stop-color="#2c2f36"/>
        </linearGradient>
        <radialGradient id="discGradient" cx="0.65" cy="0.55" r="0.6">
          <stop offset="0" stop-color="#ffffff"/>
          <stop offset="1" stop-color="#dedbd7"/>
        </radialGradient>
      </defs>
      <rect x="325" y="0" width="675" height="575" fill="url(#panelGradient)"/>
      <circle cx="281" cy="281" r="284" fill="url(#discGradient)"/>
      <circle cx="281" cy="281" r="254" fill="none" stroke="var(--ring-grey)" stroke-width="7"/>
    </svg>

    <div class="brand-mark">
      <div class="brand-circle"></div>
      <div class="brand-name">Corvane Capital</div>
    </div>

    <div class="contact-block">
      <div class="person-name">DANIEL HART</div>
      <div class="person-title">Founder &amp; CEO</div>
      <div class="divider-dots"><span></span><span></span><span></span><span></span><span></span></div>
      <ul class="contact-list">
        <li class="address">
          <svg viewBox="0 0 24 24"><path d="M12 2a7 7 0 0 0-7 7c0 5 7 13 7 13s7-8 7-13a7 7 0 0 0-7-7zm0 9.5A2.5 2.5 0 1 1 12 6.5a2.5 2.5 0 0 1 0 5z"/></svg>
          <span>88 Harbor Lane, Suite 400<br>Greenwich, CT 06830</span>
        </li>
        <li>
          <svg viewBox="0 0 24 24"><path d="M6.6 10.8a15 15 0 0 0 6.6 6.6l2.2-2.2c.3-.3.7-.4 1-.2 1.1.4 2.3.6 3.6.6.6 0 1 .4 1 1V20c0 .6-.4 1-1 1A17 17 0 0 1 3 4c0-.6.4-1 1-1h3.5c.6 0 1 .4 1 1 0 1.3.2 2.5.6 3.6.1.3 0 .7-.2 1z"/></svg>
          <span>(555) 210-4836</span>
        </li>
        <li>
          <svg viewBox="0 0 24 24"><path d="M7 2h10a2 2 0 0 1 2 2v16a2 2 0 0 1-2 2H7a2 2 0 0 1-2-2V4a2 2 0 0 1 2-2zm0 3v13h10V5z"/></svg>
          <span>(555) 210-4837</span>
        </li>
        <li>
          <svg viewBox="0 0 24 24"><path d="M7 3h10v5H7zM4 9h16a2 2 0 0 1 2 2v6h-4v4H6v-4H2v-6a2 2 0 0 1 2-2zm4 7v3h8v-3z"/></svg>
          <span>(555) 210-4838</span>
        </li>
        <li>
          <svg viewBox="0 0 24 24"><path d="M3 5h18v14H3zm2 2v.5l7 4.5 7-4.5V7l-7 4.5z"/></svg>
          <span>info@corvanecapital.com</span>
        </li>
        <li>
          <svg viewBox="0 0 24 24"><path d="M12 2a10 10 0 1 0 0 20 10 10 0 0 0 0-20zm6.9 9h-3a15 15 0 0 0-1.3-5.7A8 8 0 0 1 18.9 11zM12 4.1c.9 1.2 1.8 3.5 1.9 6.9h-3.8c.1-3.4 1-5.7 1.9-6.9zM9.4 5.3A15 15 0 0 0 8.1 11h-3a8 8 0 0 1 4.3-5.7zM5.1 13h3a15 15 0 0 0 1.3 5.7A8 8 0 0 1 5.1 13zm6.9 6.9c-.9-1.2-1.8-3.5-1.9-6.9h3.8c-.1 3.4-1 5.7-1.9 6.9zm2.6-1.2a15 15 0 0 0 1.3-5.7h3a8 8 0 0 1-4.3 5.7z"/></svg>
          <span>corvanecapital.com</span>
        </li>
      </ul>
    </div>
  </div>
</body>
</html>
```